Need CATCHY/VIVID Banner design for my new UTV/ATV/Off Road Vehicle turn signal/lighting company

I need a banner ad designed so I can advertise on several different ATV (all terrain vehicle), UTV (Utility Vehicles), Golf Cart and Off-Road Vehicle forums. Ads need to be very catchy and produce a call to action. Action is getting hits to my website. Our main business is selling turn signal kits to make your side by side or your ATV/UTV street legal, as some states now allow you to drive these on public roads if you have the following items: Turn Signals, Horn, Lighted license plate bracket, headlights and brake lights. We sell all of these items for just about any model vehicle out there. Our call to action for this banner would be to get more website visits.

Target Market(s)

Off-road/outdoor enthusiasts,

Industry/Entity Type

Car Accessorie

Font styles to use
Sans Serif

Requirements
Must have
• Ad size need to be either 728x90 or 300x250. Colorful ad with an off-road vehicle integrated to the design (think UTV, side-by-side, etc.
Nice to have
• Nice to haves would be anything that makes this banner ad stand out on very boring web pages.
Should not have
• anything dull

```html
<!DOCTYPE html>
<html lang="en">
<head>
<meta charset="utf-8">
<title>TrailBlink Banner Ads</title>
<link rel="stylesheet" href="https://fonts.googleapis.com/css2?family=Outfit:wght@700&display=swap">
<style>
  :root {
    --stage: #222222;
    --red: #e20613;
    --yellow: #ffc000;
    --ink: #141414;
    --white: #ffffff;
    --sky-top: #6f7886;
    --sky-low: #c4ccd6;
    --sea: #2f6e9e;
    --rock: #3a3a3c;
    --vehicle-red: #d8331c;
    --vehicle-grey: #8d8a80;
  }
  * { margin: 0; padding: 0; box-sizing: border-box; }
  html, body { width: 1200px; height: 995px; overflow: hidden; background: var(--stage); }
  body { position: relative; font-family: "Outfit", sans-serif; }

  .ad {
    position: absolute;
    transform: scale(0.96);
    transform-origin: top left;
    overflow: hidden;
    box-shadow: 0 6px 16px rgba(0,0,0,0.55);
  }
  .ad-rectangle { left: 456px; top: 276px; width: 300px; height: 250px; }
  .ad-leaderboard { left: 251px; top: 590px; width: 728px; height: 90px; }
  .ad svg.shapes { position: absolute; inset: 0; }

  .shop-button {
    position: absolute;
    display: flex; align-items: center; justify-content: center;
    background: var(--ink);
    color: var(--white);
    font-weight: 700;
    font-size: 24px;
    line-height: 1;
    letter-spacing: -0.3px;
    border-radius: 2px;
    text-decoration: none;
  }
  .ad-rectangle .shop-button { left: 69px; top: 192px; width: 168px; height: 36px; }
  .ad-leaderboard .shop-button { left: 301px; top: 29px; width: 168px; height: 36px; }

  .brand {
    position: absolute;
    display: flex; align-items: center; gap: 7px;
    background: var(--ink);
    color: var(--white);
    font-weight: 700;
    line-height: 1;
    letter-spacing: 0.6px;
    white-space: nowrap;
  }
  .brand-square { width: 13px; height: 13px; background: var(--yellow); flex: none; }
  .ad-rectangle .brand { left: 156px; top: 8px; padding: 7px 10px; font-size: 16px; }
  .ad-leaderboard .brand { left: 506px; top: 28px; padding: 8px 14px; font-size: 21px; }
</style>
</head>
<body>

<section class="ad ad-rectangle">
  <svg class="shapes" width="300" height="250" viewBox="0 0 300 250">
    <defs>
      <linearGradient id="sceneRect" x1="0" y1="0" x2="0" y2="1">
        <stop offset="0" stop-color="var(--sky-top)"/>
        <stop offset="0.45" stop-color="var(--sky-low)"/>
        <stop offset="0.55" stop-color="var(--sea)"/>
        <stop offset="0.75" stop-color="var(--rock)"/>
        <stop offset="1" stop-color="#2a2a2c"/>
      </linearGradient>
      <radialGradient id="subjectRect" cx="0.5" cy="0.5" r="0.5">
        <stop offset="0" stop-color="var(--vehicle-red)" stop-opacity="0.95"/>
        <stop offset="0.45" stop-color="var(--vehicle-grey)" stop-opacity="0.8"/>
        <stop offset="1" stop-color="var(--vehicle-grey)" stop-opacity="0"/>
      </radialGradient>
      <clipPath id="sceneClipRect">
        <polygon points="0,0 300,0 300,148 154,172 0,148"/>
      </clipPath>
    </defs>
    <g class="vehicle-photo" role="img" aria-label="Photo of a red and grey side-by-side UTV with glowing yellow lights on dark rocks by the sea" clip-path="url(#sceneClipRect)">
      <rect width="300" height="172" fill="url(#sceneRect)"/>
      <ellipse cx="150" cy="92" rx="125" ry="82" fill="url(#subjectRect)"/>
    </g>
    <polygon points="0,148 154,172 300,148 300,250 0,250" fill="var(--yellow)"/>
    <polygon points="0,157 154,180 300,157 300,250 0,250" fill="var(--red)"/>
    <polygon points="0,225 95,250 0,250" fill="var(--yellow)"/>
    <polygon points="212,250 300,230 300,250" fill="var(--yellow)"/>
  </svg>
  <div class="brand"><span class="brand-square"></span>TRAILBLINK</div>
  <a class="shop-button" href="#">SHOP NOW</a>
</section>

<section class="ad ad-leaderboard">
  <svg class="shapes" width="728" height="90" viewBox="0 0 728 90">
    <defs>
      <linearGradient id="sceneWide" x1="0" y1="0" x2="0" y2="1">
        <stop offset="0" stop-color="var(--sky-top)"/>
        <stop offset="0.4" stop-color="var(--sky-low)"/>
        <stop offset="0.5" stop-color="var(--sea)"/>
        <stop offset="0.65" stop-color="var(--rock)"/>
        <stop offset="1" stop-color="#2a2a2c"/>
      </linearGradient>
      <radialGradient id="subjectWide" cx="0.5" cy="0.5" r="0.5">
        <stop offset="0" stop-color="var(--vehicle-red)" stop-opacity="0.95"/>
        <stop offset="0.45" stop-color="var(--vehicle-grey)" stop-opacity="0.8"/>
        <stop offset="1" stop-color="var(--vehicle-grey)" stop-opacity="0"/>
      </radialGradient>
      <clipPath id="sceneClipWide">
        <polygon points="0,0 220,0 258,45 220,90 0,90"/>
      </clipPath>
    </defs>
    <rect width="728" height="90" fill="var(--red)"/>
    <polygon points="0,0 233,0 271,45 233,90 0,90" fill="var(--yellow)"/>
    <g class="vehicle-photo" role="img" aria-label="Photo of a side-by-side UTV on dark volcanic rock by the sea" clip-path="url(#sceneClipWide)">
      <rect width="260" height="90" fill="url(#sceneWide)"/>
      <ellipse cx="122" cy="50" rx="70" ry="46" fill="url(#subjectWide)"/>
    </g>
    <rect x="724" y="0" width="4" height="90" fill="var(--yellow)"/>
  </svg>
  <a class="shop-button" href="#">SHOP NOW</a>
  <div class="brand"><span class="brand-square"></span>TRAILBLINK</div>
</section>

</body>
</html>
```